Web Design Project

We are looking for a unified design of Corporate Website, Stationary (Including Letterhead and Envelopes), Business Cards, Email Footers and Sales & Marketing Brochures.

Color palette should include:
Black (R: 24, G:24, B:24)
Red (R:206, G:0, B:39)
Dark Grey (R:51, G:51, B:51)
Light Grey/Silver (R:203, G:203, B:203)

As we do business in North America and the UK, designs should be reflective of standard sizing for both regions.

Check out our website to better understand who we are: www.KLVR.com and a copy of our Logo has been uploaded for reference.
Updates

Hello all, we had not anticipated the volume of unique, high quality designs we have received, thank you all for your submissions. A team review of all designs will take place the week of December 8th, and final decisions and selections made. Thank you again

Target Market(s)

Automotive Parts Wholesalers, Vehicle Repair Specialists, Automotive Parts Manufacturers, Automotive Insurance

Industry/Entity Type

Business

Font styles to use
Sans Serif

Requirements
Must have
• - Color palette should include:
- Black (R: 24, G:24, B:24)
- Red (R:206, G:0, B:39)
- Dark Grey (R:51, G:51, B:51)
- Light Grey/Silver (R:203, G:203, B:203)
Should not have
• No Animations

```html
<!DOCTYPE html>
<html lang="en">
<head>
<meta charset="utf-8">
<title>Kelvar Parts Solutions</title>
<link rel="stylesheet" href="https://fonts.googleapis.com/css2?family=Montserrat:wght@400;600;700&family=Questrial&display=swap">
<style>
:root{
  --black:#181818;
  --red:#ce0027;
  --dark-grey:#333333;
  --silver:#cbcbcb;
  --panel:#eceef0;
  --strip:#e6e6e6;
  --white:#ffffff;
}
*{box-sizing:border-box;margin:0;padding:0}
html,body{width:722px;height:1200px;overflow:hidden}
body{position:relative;background:linear-gradient(#f0f0f0 230px,#fff 380px);font-family:'Questrial',sans-serif;color:var(--black)}
.top-band{position:absolute;left:0;top:0;width:722px;height:230px;background:var(--red)}
.header{position:absolute;left:60px;top:14px;width:601px;height:45px;background:var(--white)}
.brand{position:absolute;left:16px;top:12px;display:flex;align-items:center;gap:6px;font-family:'Montserrat',sans-serif;font-weight:700;font-size:14px;color:var(--dark-grey)}
.brand-dot{width:20px;height:20px;border-radius:50%;border:3px solid #9a9a9a}
.utility{position:absolute;right:6px;top:6px;font-family:'Montserrat',sans-serif;font-size:6.5px;font-weight:600;color:var(--black)}
.lang{position:absolute;right:8px;top:20px;width:38px;height:16px;border:1px solid var(--silver);border-radius:2px;background:#fafafa}
.lang i{position:absolute;left:4px;top:4px;width:14px;height:8px;background:var(--red)}
.nav{position:absolute;left:60px;top:59px;width:601px;height:43px;background:linear-gradient(#3a3a3a,#111);display:flex}
.nav a{display:flex;align-items:center;padding:0 13px;font-family:'Montserrat',sans-serif;font-weight:600;font-size:7px;color:var(--white);text-decoration:none;border-right:1px solid #2a2a2a}
.nav a.active{color:var(--red);background:#111}
.hero{position:absolute;left:60px;top:102px;width:601px;height:240px;border:2px solid var(--black);background:linear-gradient(110deg,#5a5a5a,#d8d8d8 35%,#8a8a8a 60%,#c9c08a 80%,#e8e8e8);box-shadow:0 18px 18px -12px rgba(0,0,0,.35)}
.hero-caption{position:absolute;left:145px;top:105px;width:306px;height:48px;background:rgba(206,0,39,.85);color:var(--white);font-size:21px;display:flex;align-items:center;justify-content:center;letter-spacing:.5px}
.hero-dots{position:absolute;left:246px;top:220px;width:106px;height:18px;background:rgba(0,0,0,.6);border-radius:10px 10px 0 0;display:flex;justify-content:center;align-items:center;gap:6px}
.hero-dots i{width:7px;height:7px;border-radius:50%;background:var(--black);border:1px solid #777}
.hero-dots i.on{background:var(--white)}
.markets{position:absolute;left:55px;top:385px;width:620px;display:flex;justify-content:space-between}
.market{width:195px;text-align:center}
.market-art{width:80px;height:80px;margin:0 auto 12px;border-radius:8px}
.market h2{font-family:'Montserrat',sans-serif;font-weight:400;font-size:13px;line-height:18px;color:var(--red)}
.market h2 span{display:block;color:var(--dark-grey)}
.market p{margin:8px auto 0;width:185px;font-size:7.3px;line-height:11px;color:var(--black)}
.testimonials{position:absolute;left:60px;top:615px;width:602px;height:140px;background:var(--white);box-shadow:0 -8px 10px -10px rgba(0,0,0,.25),0 8px 10px -10px rgba(0,0,0,.25);text-align:center}
.testimonials h3{margin-top:16px;font-family:'Montserrat',sans-serif;font-weight:600;font-size:12.5px}
.testimonials blockquote{margin:10px auto 0;width:430px;font-size:9.6px;line-height:18px}
.testimonials cite{display:block;margin-top:8px;font-style:normal;font-size:10px;color:var(--red)}
.t-dots{display:flex;justify-content:center;gap:6px;margin-top:10px}
.t-dots i{width:6px;height:6px;border-radius:50%;background:var(--silver)}
.t-dots i.on{background:var(--red)}
.card{position:absolute;top:793px;width:161px;height:280px}
.card-art{width:161px;height:107px}
.card h3{position:absolute;left:5px;top:117px;width:180px;white-space:nowrap;font-family:'Montserrat',sans-serif;font-weight:700;font-size:15px;line-height:18px;color:var(--red)}
.card p{position:absolute;left:6px;top:172px;width:168px;font-size:6.9px;line-height:14.2px;color:var(--black)}
.btn{position:absolute;left:6px;top:252px;width:57px;height:19px;background:var(--black);color:var(--white);font-size:7.5px;display:flex;align-items:center;justify-content:center}
.rewards{position:absolute;left:436px;top:793px;width:227px;height:280px;background:var(--panel);border:1px solid #d9dbde;padding:0 20px 0 26px}
.rewards-brand{margin-top:36px;display:flex;align-items:center;gap:6px;font-family:'Montserrat',sans-serif;font-weight:700;font-size:10px;color:var(--red)}
.rewards-brand i{width:24px;height:24px;border-radius:50%;background:var(--red)}
.rewards h3{margin-top:22px;font-family:'Montserrat',sans-serif;font-weight:600;font-size:15px;line-height:21px;color:var(--black)}
.rewards h3 span{color:var(--red)}
.rewards p{margin-top:8px;font-size:9.3px;line-height:14.5px}
.partners{position:absolute;left:0;top:1090px;width:722px;height:56px;background:var(--strip);display:flex;justify-content:center;align-items:center;gap:24px}
.partners span{font-family:'Montserrat',sans-serif;font-weight:600;font-size:8px;color:#4a4a4a;letter-spacing:.5px}
.footer{position:absolute;left:0;top:1146px;width:722px;height:54px;background:var(--red);color:var(--white)}
.footer-nav{position:absolute;left:59px;top:12px;font-size:7.3px}
.footer-nav b{font-weight:400;margin:0 6px}
.copyright{position:absolute;left:59px;top:29px;font-size:7.3px}
.social{position:absolute;left:619px;top:17px;display:flex;gap:3px}
.social i{width:20px;height:20px;border-radius:50%;background:var(--white)}
</style>
</head>
<body>
<div class="top-band"></div>

<header class="header">
  <div class="brand"><span class="brand-dot"></span>KELVAR PARTS SOLUTIONS</div>
  <div class="utility">SUPPLIER LOGIN &nbsp;|&nbsp; KELVAR AWARDS</div>
  <div class="lang"><i></i></div>
</header>

<nav class="nav">
  <a class="active">HOME</a>
  <a>INTELLIGENT SALES &amp; MARKETING</a>
  <a>KELVAR AWARDS</a>
  <a>REFERENCES</a>
  <a>ABOUT US</a>
  <a>CAREERS</a>
  <a>CONTACT US</a>
</nav>

<section class="hero" role="img" aria-label="Close-up photograph of machined engine parts on a factory line">
  <div class="hero-caption">Genuine Sales &amp; Marketing</div>
  <div class="hero-dots"><i class="on"></i><i></i><i></i><i></i><i></i></div>
</section>

<section class="markets">
  <div class="market">
    <div class="market-art" role="img" aria-label="Car engine illustration" style="background:radial-gradient(#8a8a8a,#2b2b2b 70%,#fff 71%)"></div>
    <h2>AUTOMOTIVE<span>PARTS WHOLESALERS</span></h2>
    <p>Lorem Ipsum has been the industry's standard dummy text ever since the 1500s, when an unknown printer took a galley of type and scrambled it to make a type specimen book</p>
  </div>
  <div class="market">
    <div class="market-art" role="img" aria-label="Tyre with wrench and screwdriver" style="background:radial-gradient(#b0b0b0 25%,#222 45%,#fff 60%)"></div>
    <h2>VEHICLE<span>REPAIR SPECIALISTS</span></h2>
    <p>Lorem Ipsum has been the industry's standard dummy text ever since the 1500s, when an unknown printer took a galley of type and scrambled it to make a type specimen book</p>
  </div>
  <div class="market">
    <div class="market-art" role="img" aria-label="Yellow industrial robot arm" style="background:radial-gradient(#e8b400 20%,#c9a23a 40%,#fff 62%)"></div>
    <h2>AUTOMOTIVE<span>PARTS MANUFACTURERS</span></h2>
    <p>Lorem Ipsum has been the industry's standard dummy text ever since the 1500s, when an unknown printer took a galley of type and scrambled it to make a type specimen book</p>
  </div>
</section>

<section class="testimonials">
  <h3>TESTIMONIALS</h3>
  <blockquote>Harbor Group has contracted with Kelvar DataSystems as our wholesale representative company for many years...</blockquote>
  <cite>Dan Morrow, Parts Manager Summit Motors</cite>
  <div class="t-dots"><i class="on"></i><i></i><i></i><i></i><i></i></div>
</section>

<article class="card" style="left:77px">
  <div class="card-art" role="img" aria-label="Compass with an opportunity label" style="background:linear-gradient(135deg,#6b4a1c,#d9b26a 50%,#7a5520)"></div>
  <h3 style="top:120px">The Opportunity</h3>
  <p>OE Wholesale Parts provide significant opportunities for both OE dealership suppliers and repairers to capture new and incremental profits.</p>
  <div class="btn">Read More</div>
</article>

<article class="card" style="left:262px">
  <div class="card-art" role="img" aria-label="Businesswoman breaking a finish-line ribbon" style="background:linear-gradient(160deg,#6fa0d8,#2c63b8 60%,#c81e2a)"></div>
  <h3>The Kelvar<br>Multi-Brand Solution</h3>
  <p>We offer a unique multi-brand solution to both OE suppliers and the automotive repairers by combining professionally managed parts programs that are shared between non-competing suppliers.</p>
  <div class="btn">Read More</div>
</article>

<aside class="rewards">
  <div class="rewards-brand"><i></i>KELVAR AWARDS</div>
  <h3>Kelvar Parts<br><span>Rewards</span></h3>
  <p>Our Kelvar Awards wholesale parts loyalty program is designed specifically for the automotive repair industry. Repairers earn Reward Points from multiple suppliers, not just one earning bigger, better Rewards faster than any other program in our industry.</p>
</aside>

<section class="partners">
  <span>NORVIK</span><span>TESSAN</span><span>HARUKA</span><span>MAZENO</span><span>SORELL</span><span>MERIDIAN</span><span>LUMEN</span><span>JORVAN</span><span>IZARO</span>
</section>

<footer class="footer">
  <div class="footer-nav">Home<b>|</b>Intelligent Sales &amp; Marketing<b>|</b>Kelvar Awards<b>|</b>References<b>|</b>About Us<b>|</b>Careers<b>|</b>Contact Us</div>
  <div class="copyright">Copyright © 1998 - 2014 Kelvar Parts Solutions</div>
  <div class="social"><i></i><i></i></div>
</footer>
</body>
</html>
```